Lotstallmart.com Webpage Design

Design Brief for lotstallmart.com (Copy of Brief also in attached Word file)

Name of Website- lotstallmart.com (existing logo and look & feel of website to be changed)

Logo - Finalised. The logo files are attached with the brief as “logo.jpeg”. The “Blue- Grey” version of the logo is for use on lighter backgrounds and the “Orange-White” version of the logo is for use on darker backgrounds. (A full Black version of the logo is also attached). Both versions may be used in different parts of the website. All attached files are in .png format.
Status - The website in functional and is undergoing user trials. However, we want to improve the look & feel of the website so at it seems
a. cotemporary,
b. Easy to Navigate
c. professional and
d. Vibrant.

Please visit ‘lotstallmart.com’ to check out the website and its functionalities – please use it only as a reference for the features & functions to be provided, however the designer should use a ‘Free Hand’ in designing the composition of various parts of the webpage without getting too influenced by the existing design

Objective of the Website ‘lotstallmart.com –
a. It is a portal focussed on listing of ‘Retail’ specific real-estate properties by developers, owners and realty brokers. The properties shall listed under the following four categories-
i. Retail Malls
ii. Shopping Complexes
iii. High-street shops
iv. Retail Warehouses
*refer lotstallmart.com for better clarity

b. The abovementioned properties shall be listed either for ‘Sale’ or ‘rent\lease’ or both

c. Users shall visit the site in case they wish to acquire a retail \ shop space either on ‘sale’ or ‘rent’. These Users would be able to specify the ‘Search Criteria’ through the tool-bars provided on the website – the ‘Search Criteria’ shall comprise of ‘Type of space category’, ‘City’, ‘Locality’, transaction type ie ‘Rent \ Sale’ and ‘Area Range’

d. The main revenue model for the website shall be listing fee ( or advertising charges ) payable by those listing their properties on the website.

Three Main Pages of Website (lotstallmart.com) that need to be designed -
a. Main Home Page (visit the web link - http://lotstallmart.com/ ) - The main home page has the “Search Toolbar” for specifying of Search Criteria by the User. It shall also have the following features & functions-
i. Main Advertising Banner
ii. Featured Projects
iii. New Launches
iv. Toolbar with buttons – ‘Advertise with Us’, ‘Listings Alert’, ‘Mart Wizards’, ‘Advertiser Login’

b. Property Listings Page (visit the web link - http://lotstallmart.com/gurgaon-in-india ) - The List of property options that match the Criteria specified by the ‘User’ get displayed on this page.

c. Property Detail Page - When the ‘User’ clicks on the “More….” Button on the ‘Property Listings Page’ (given in point b. above) the web page with the details of the property opens. (For Example – visit the web link - http://lotstallmart.com/vorne-Shopping-Complex-vorne-quadrion-gurgaon-636 )

Note:- Please refer to attached ‘Shopping’ related images the designer may use them on the website to provide a look & feel of retail if required – either separately or rotate in a single window

Target Market(s)

Retailers & Investors looking for retail space, Real Estate Brokers, Developers

Industry/Entity Type

Advertising

Number of Pages Required

3 page

Requirements
Must have
• Refer to existing site lotstallmart.com -- all the existing functionalities are a must have.
Nice to have
• The Designer may use the retail related images on the website if required for making it more vibrant. Refer attached images Shopping(1-6).jpg

```html
<!DOCTYPE html>
<html lang="en">
<head>
<meta charset="utf-8">
<title>Lotstallmart.com – Retail Space Portal</title>
<link href="https://fonts.googleapis.com/css2?family=Open+Sans:wght@400;600;700;800&display=swap" rel="stylesheet">
<style>
:root{
  --navy:#1c2530;
  --navy-2:#242f3b;
  --topbar:#222b35;
  --blue:#1a8fe3;
  --blue-light:#cfe9fb;
  --grey-bg:#e8e8e8;
  --beige:#efe6d9;
  --text:#1e1e1e;
  --white:#fff;
}
*{box-sizing:border-box;margin:0;padding:0}
html,body{width:1200px;height:2416px;overflow:hidden}
body{font-family:"Open Sans",Arial,sans-serif;color:var(--text);background:#fff}
.wrap{width:782px;margin:0 auto;position:relative}

/* top bar */
.topbar{height:29px;background:var(--topbar);color:#dfe6ee;font-size:13px}
.topbar .wrap{display:flex;align-items:center;height:29px;width:980px}
.topbar .contact{display:flex;gap:36px;margin-left:110px}
.topbar .contact span{display:flex;align-items:center;gap:6px}
.topbar .right{margin-left:auto;display:flex;gap:10px;align-items:center}
.topbar .login{background:#36414d;padding:3px 10px;border-radius:2px}

/* nav */
.nav{height:61px;background:var(--navy);border-top:1px solid #333e4a}
.nav .wrap{display:flex;align-items:center;height:61px;width:980px}
.brand{display:flex;align-items:center;gap:8px;margin-left:110px}
.brand .dot{width:30px;height:30px;border-radius:50%;background:var(--blue)}
.brand .name{color:var(--white);font-weight:700;font-size:26px;letter-spacing:-.5px}
.menu{margin-left:auto;display:flex;gap:30px;font-size:13px;color:#dfe6ee;margin-right:30px}
.menu .active{border-bottom:1px solid #fff;padding-bottom:2px}

/* hero */
.hero{height:442px;position:relative;background:linear-gradient(180deg,#7d8287 0%,#9ea3a7 35%,#6f7479 75%,#54595e 100%)}
.hero-photo{position:absolute;inset:0}
.tabs{position:absolute;left:250px;top:132px;display:flex;gap:4px}
.tabs span{display:block;width:96px;height:36px;line-height:36px;text-align:center;font-size:19px;color:#fff;background:#1d242c;border-radius:4px 4px 0 0}
.tabs .on{background:var(--blue)}
.search{position:absolute;left:238px;top:168px;width:725px;height:64px;background:#1e2731;border:1px solid #3d4956;border-radius:3px;display:flex;align-items:flex-end;padding:0 10px 10px;gap:10px}
.field{display:flex;flex-direction:column;align-items:center;font-size:10.5px;color:#dfe6ee;gap:4px;white-space:nowrap}
.field .box{height:32px;background:#fff;color:#333;font-size:12.5px;display:flex;align-items:center;justify-content:space-between;padding:0 8px;width:100%;overflow:hidden}
.field .box.ph{color:#999;font-size:9.5px;padding:0 6px}
.caret{width:0;height:0;border-left:4px solid transparent;border-right:4px solid transparent;border-top:4px solid #333}
.btn-search{height:32px;width:102px;background:var(--blue);color:#fff;font-size:15px;display:flex;align-items:center;justify-content:center}
.toolbar{position:absolute;left:314px;top:245px;width:572px;height:42px;background:#2b3540;border:1px solid #46525f;border-radius:3px;display:flex}
.toolbar .item{flex:1;display:flex;align-items:center;justify-content:center;gap:12px;color:#fff;font-size:13.5px;border-right:1px solid #46525f}
.toolbar .item:last-child{border-right:0}
.toolbar small{display:block;color:var(--blue);font-size:9px;font-style:italic}

/* categories */
.cats{height:83px;background:var(--navy-2);display:flex;justify-content:center;align-items:center;border-top:2px solid #35404c}
.cats .cat{width:150px;height:48px;margin:0 30px;background:#2e3a47;border:1px solid #3e4b59;display:flex;flex-direction:column;justify-content:center;align-items:center}
.cats .cat b{color:var(--blue);font-weight:400;font-size:13px}
.cats .cat small{color:#dfe6ee;font-size:9.5px}
.cats .sep{width:1px;height:60px;background:#3e4b59}

/* listings */
.listing{padding-top:27px}
.listing.featured{height:564px;background:var(--grey-bg)}
.listing.launches{height:561px;background:#fff;padding-top:10px}
.listing h2{font-size:18px;font-weight:700;margin-bottom:8px}
.listing h2 span{font-weight:400;font-size:15px}
.grid{display:grid;grid-template-columns:repeat(3,250px);gap:20px 16px}
.card{height:214px;background:#fff;border:1px solid #c9c9c9;box-shadow:0 1px 3px rgba(0,0,0,.2);padding:7px}
.card .photo{height:129px}
.card .info{height:64px;background:var(--blue-light);padding:3px 8px;position:relative;font-size:10px;line-height:13px;color:#444}
.card .city{font-size:17px;font-weight:700;color:#111;line-height:20px}
.card .proj{font-weight:700;color:#222;white-space:nowrap}
.card .view{position:absolute;right:8px;top:22px;background:var(--blue);color:#fff;font-size:10px;padding:1px 8px;border-radius:3px}
.view-all{display:inline-block;margin:14px 0 0 8px;background:var(--navy);color:#fff;font-size:12px;padding:4px 16px}
.p1{background:linear-gradient(180deg,#4a5f9e,#b88a45 70%,#2a2a35)}
.p2{background:linear-gradient(180deg,#3b4f7a,#c7924f 60%,#3f4a3a)}
.p3{background:linear-gradient(180deg,#9fb8c9,#7d8c96 60%,#5d6d58)}
.p4{background:linear-gradient(180deg,#b6c6d6,#8c8f6b 60%,#6c6e68)}
.p5{background:linear-gradient(180deg,#9db3c6,#a5524d 55%,#4e6a3a)}
.p6{background:linear-gradient(180deg,#8fb6d9,#c4cfd6 55%,#7c8b6c)}

/* help */
.help{height:180px;background:linear-gradient(180deg,#2c3540,#3e4751 50%,#2a323c)}
.help h3{text-align:center;color:#fff;font-size:22px;font-weight:700;padding-top:28px}
.help .items{display:flex;justify-content:center;gap:70px;margin-top:22px}
.help .item{display:flex;align-items:center;gap:8px;color:#fff;font-weight:700;font-size:14px}

/* info section */
.info-sec{height:322px;background:var(--beige);padding-top:14px}
.info-sec .wrap{display:flex;gap:100px}
.col-l{width:300px}
.col-r{width:382px}
.info-sec h4{font-size:17px;font-weight:600;margin-bottom:6px}
.info-sec p{font-size:11px;line-height:14px;color:#333}
.form{display:flex;margin-top:10px}
.form .in{height:29px;width:203px;background:#fff;border:1px solid #ccc;font-size:11px;color:#999;display:flex;align-items:center;padding-left:10px}
.form .go{height:29px;width:97px;background:var(--blue);color:#fff;font-size:12px;display:flex;align-items:center;justify-content:center}
.btn-more{display:inline-block;background:var(--navy);color:#fff;font-size:12px;padding:4px 18px;margin:10px 0 20px}

/* footer */
.footer{height:155px;background:var(--navy);color:#fff}
.footer .wrap{display:flex;padding-top:30px}
.footer .flogo{width:287px;display:flex;align-items:center;gap:8px;padding-top:20px;height:60px}
.footer .flogo .dot{width:30px;height:30px;border-radius:50%;background:var(--blue)}
.footer .flogo span{font-size:26px;font-weight:700;color:#2b82c4}
.fcol{font-size:11px;line-height:17px}
.fcol h5{font-size:13px;font-weight:700;margin-bottom:4px}
.fcol.addr{width:205px}
.fcol.co{width:155px}
.social{display:flex;gap:4px;margin:4px 0 10px}
.social i{width:17px;height:17px;border:1.5px solid #fff;border-radius:50%;display:block}
.copy{height:19px;background:#111820;color:#8a929b;font-size:9.5px;text-align:center;line-height:19px}
</style>
</head>
<body>

<header>
  <div class="topbar"><div class="wrap">
    <div class="contact">
      <span><svg width="14" height="10" viewBox="0 0 14 10"><rect x=".5" y=".5" width="13" height="9" fill="none" stroke="#1a8fe3"/><path d="M.5 .5 7 6 13.5.5" fill="none" stroke="#1a8fe3"/></svg>contact@lotstallmart.com</span>
      <span><svg width="11" height="12" viewBox="0 0 11 12"><path d="M2 0h2l1 3-1.5 1a6 6 0 0 0 3.5 3.5L8 6l3 1v2c0 1-1 2-2 2C4 11 0 7 0 2c0-1 1-2 2-2z" fill="#1a8fe3"/></svg>1-877-555-0142</span>
    </div>
    <div class="right"><span class="login">Advertiser Login</span><span>All India ▾</span></div>
  </div></div>
  <nav class="nav"><div class="wrap">
    <div class="brand"><span class="dot"></span><span class="name">lotstallmart</span></div>
    <div class="menu"><span class="active">Home</span><span>About Us</span><span>Featured Projects</span><span>New Launches</span><span>Contact Us</span></div>
  </div></nav>
</header>

<section class="hero">
  <div class="hero-photo" role="img" aria-label="Greyscale city skyline with high-rise towers"></div>
  <div class="tabs"><span class="on">Sale</span><span>Rent</span><span>Both</span></div>
  <div class="search">
    <div class="field" style="width:143px">Retail Format<div class="box">Retail Malls<i class="caret"></i></div></div>
    <div class="field" style="width:84px">Select City<div class="box">Select<i class="caret"></i></div></div>
    <div class="field" style="width:194px">Select Locality/Micro-Market<div class="box">Select<i class="caret"></i></div></div>
    <div class="field" style="width:153px">Enter Keywords<div class="box ph">Name of Project, Develoer etc.</div></div>
    <div class="btn-search">SEARCH</div>
  </div>
  <div class="toolbar">
    <div class="item"><svg width="22" height="18" viewBox="0 0 22 18"><path d="M0 9 22 0v18z" fill="#1a8fe3"/></svg><span>Advertise with us<small>Standard listing - FREE</small></span></div>
    <div class="item"><svg width="20" height="18" viewBox="0 0 20 18"><rect x="1" y="6" width="18" height="12" fill="#1a8fe3"/><path d="M0 6 3 0h14l3 6z" fill="#1a8fe3"/></svg><span>Mart Wizards<small>Shop Search Services</small></span></div>
    <div class="item"><svg width="20" height="18" viewBox="0 0 20 18"><path d="M10 0 20 18H0z" fill="#1a8fe3"/><rect x="9" y="6" width="2" height="6" fill="#fff"/><rect x="9" y="14" width="2" height="2" fill="#fff"/></svg><span>Listing Alert</span></div>
  </div>
</section>

<section class="cats">
  <div class="cat"><b>Retail Malls</b><small>Centrally Air-Conditioned</small></div><span class="sep"></span>
  <div class="cat"><b>Shopping Complex</b><small>Non Air-Conditioned Building</small></div><span class="sep"></span>
  <div class="cat"><b>High Street Shops</b><small>Road Facing Retail</small></div><span class="sep"></span>
  <div class="cat"><b>Retail Warehouses</b><small>Back-end Retail Storage</small></div>
</section>

<section class="listing featured"><div class="wrap">
  <h2>Featured Retail Projects <span>(Across India)</span></h2>
  <div class="grid">
    <div class="card"><div class="photo p1" role="img" aria-label="Tall retail tower lit at dusk"></div><div class="info"><div class="city">Surat</div><div class="proj">Orvanta</div>Althan<br>Shopping Complex<span class="view">View the listing</span></div></div>
    <div class="card"><div class="photo p2" role="img" aria-label="Hotel and mall building at night"></div><div class="info"><div class="city">Faridabad</div><div class="proj">Kestrel 81 High Street</div>Sector-81<br>Shopping Complex<span class="view">View the listing</span></div></div>
    <div class="card"><div class="photo p3" role="img" aria-label="Glass towers beside an elevated metro line"></div><div class="info"><div class="city">Gurgaon</div><div class="proj">Lumora Plaza</div>Sector-65<br>Shopping Complex<span class="view">View the listing</span></div></div>
    <div class="card"><div class="photo p4" role="img" aria-label="Low-rise shopping complex facade"></div><div class="info"><div class="city">Surat</div><div class="proj">Orvanta</div>Althan<br>Shopping Complex<span class="view">View the listing</span></div></div>
    <div class="card"><div class="photo p5" role="img" aria-label="High street shopfronts with palm trees"></div><div class="info"><div class="city">pune</div><div class="proj">Kestrel 81 High Street</div>Sector-81<br>Shopping Complex<span class="view">View the listing</span></div></div>
    <div class="card"><div class="photo p6" role="img" aria-label="Modern glass mall entrance plaza"></div><div class="info"><div class="city">Hyderabad</div><div class="proj">Lumora Plaza</div>Sector-65<br>Shopping Complex<span class="view">View the listing</span></div></div>
  </div>
  <span class="view-all">View all</span>
</div></section>

<section class="listing launches"><div class="wrap">
  <h2>Featured New Launches <span>(Across India)</span></h2>
  <div class="grid">
    <div class="card"><div class="photo p1" role="img" aria-label="Tall retail tower lit at dusk"></div><div class="info"><div class="city">Surat</div><div class="proj">Kestrel 81 High Street</div>Sector-81<br>Shopping Complex<span class="view">View the listing</span></div></div>
    <div class="card"><div class="photo p2" role="img" aria-label="Hotel and mall building at night"></div><div class="info"><div class="city">Faridabad</div><div class="proj">Kestrel 81 High Street</div>Sector-81<br>Shopping Complex<span class="view">View the listing</span></div></div>
    <div class="card"><div class="photo p3" role="img" aria-label="Glass towers beside an elevated metro line"></div><div class="info"><div class="city">Gurgaon</div><div class="proj">Kestrel 81 High Street</div>Sector-81<br>Shopping Complex<span class="view">View the listing</span></div></div>
    <div class="card"><div class="photo p4" role="img" aria-label="Low-rise shopping complex facade"></div><div class="info"><div class="city">Surat</div><div class="proj">Orvanta</div>Althan<br>Shopping Complex<span class="view">View the listing</span></div></div>
    <div class="card"><div class="photo p5" role="img" aria-label="High street shopfronts with palm trees"></div><div class="info"><div class="city">Vjayawada</div><div class="proj">Kestrel 81 High Street</div>Sector-81<br>Shopping Complex<span class="view">View the listing</span></div></div>
    <div class="card"><div class="photo p6" role="img" aria-label="Modern glass mall entrance plaza, Editor's Choice"></div><div class="info"><div class="city">Hyderabad</div><div class="proj">Lumora Plaza</div>Sector-65<br>Shopping Complex<span class="view">View the listing</span></div></div>
  </div>
  <span class="view-all">View all</span>
</div></section>

<section class="help">
  <h3>JUST IN CASE YOU NEED ANY HELP</h3>
  <div class="items">
    <div class="item"><svg width="42" height="42" viewBox="0 0 42 42"><circle cx="21" cy="21" r="19" fill="none" stroke="#1a8fe3" stroke-width="2"/><rect x="11" y="14" width="20" height="14" fill="none" stroke="#1a8fe3" stroke-width="2"/><path d="M11 14l10 8 10-8" fill="none" stroke="#1a8fe3" stroke-width="2"/></svg>EMAIL SUPPORT</div>
    <div class="item"><svg width="42" height="42" viewBox="0 0 42 42"><circle cx="21" cy="21" r="19" fill="none" stroke="#1a8fe3" stroke-width="2"/><text x="21" y="26" text-anchor="middle" font-size="12" font-weight="700" fill="#1a8fe3" font-family="Open Sans,sans-serif">24</text></svg>24/7 SUPPORT</div>
    <div class="item"><svg width="42" height="42" viewBox="0 0 42 42"><circle cx="21" cy="21" r="19" fill="none" stroke="#1a8fe3" stroke-width="2"/><path d="M14 11h4l2 5-3 2a11 11 0 0 0 6 6l2-3 5 2v4c0 2-2 3-3 3-10 0-17-7-17-16 0-1 1-3 4-3z" fill="#1a8fe3"/></svg>PHONE</div>
    <div class="item"><svg width="42" height="42" viewBox="0 0 42 42"><circle cx="21" cy="21" r="20" fill="#1a8fe3"/><text x="21" y="30" text-anchor="middle" font-size="26" font-weight="800" fill="#fff" font-family="Open Sans,sans-serif">?</text></svg>FAQ</div>
  </div>
</section>

<section class="info-sec"><div class="wrap">
  <div class="col-l">
    <h4>Listing Alert</h4>
    <p>Suscribe for Fortnightly Email update on New Listings @ Lotstallmart.com</p>
    <div class="form"><div class="in">Enter Your email address</div><div class="go">Subscribe</div></div>
    <h4 style="margin-top:22px">Mart Wizards</h4>
    <p>Post your Retail Space requirement with us and our experts shall get back with suitable options and even help you in your transaction. This is a Free Service!</p>
    <div class="form"><div class="in">Enter Your email address</div></div>
    <div class="form" style="margin-top:8px"><div class="in">Mobile</div><div class="go" style="width:68px">Send</div></div>
  </div>
  <div class="col-r">
    <h4>Editor's Choice</h4>
    <p style="margin-top:14px">A "Select" Listing of Retail Properties Handpicked by our Editors based on their own positive evaluation on parameters &amp; attributes such as Design Concept, Location, Developer, Success Potential. So Read On to Check Out for yourself .....</p>
    <span class="btn-more">More</span>
    <h4>What is lotstallmart.com</h4>
    <p>Lotstallmart.com - About Us Lotstallmart.com is a Specialised Web based platform for Retail Space, featuring properties across India under various formats such as Retail Malls, Shopping Complexes, High-street Shops...</p>
    <span class="btn-more" style="margin-top:10px">More</span>
  </div>
</div></section>

<footer>
  <div class="footer"><div class="wrap">
    <div class="flogo"><span class="dot"></span><span>lotstallmart</span></div>
    <div class="fcol addr"><h5>Address</h5>Bharat Retail Hub<br>Suite 12, 2nd Level,<br>Lorem Ipsum is simply,<br>Block-Q, Gurgaon - 100001</div>
    <div class="fcol co"><h5>Company</h5>About Us<br>Privacy Policy<br>Terms of Use<br>Contact Us<br>Site Map</div>
    <div class="fcol"><h5>Follow Us</h5><div class="social"><i></i><i></i><i></i><i></i></div>1-877-555-0142</div>
  </div></div>
  <div class="copy">Copyright © 2013 Bharat Retail Hub.com. All rights reserved</div>
</footer>

</body>
</html>
```